Create a Brochure Design for Brantley Homecare

Brantley Homecare is a subsidiary of the Brantley Care Group. This brochure is specifically for the Brantley Homecare company and brand. Create a 3 panel, A4, front and back, tri-fold brochure. This brochure will be a way to introduce our Homecare services to the community, prospective clients, and various referral partners. The brochure must be eye catching, unique in its deliverables and demonstrate both attention to detail and comfort. Our organization is sophisticated and built around warmth, care and individualized personal attention. The most important aspect of this design is to focus on creating a nurturing, warm, and inviting feel where you would want to have a Nurse or Nurse’s Aide in your own home or a loved one’s home.

I am open to the creativity of the designer to develop something based on the above criteria; however I would like the design to work well with the existing collateral material. What I mean by that is that while I want everything to have its own personality and stand out as its own brand representative, I still need to be able to tell that the overall design concept stays stylistically inside of the same ‘family’ of existing designed material. Because of this, below I would like for the designer to pull inspiration from the link to our website (Located below) as well as from the attachment of our recently refreshed business cards (Attached). This should allow each design to be unique and creative, while still staying inside of a framework and the feel/style that I am looking for.

Finally, I want all the designers to understand that this brochure design is for a private, in home, healthcare company where we are responsible for providing personalized care for a culturally and ethnically diverse make-up clientele of all ages. The photos that are used must represent an image of warmth, care, and a positive interaction between client and caregiver.

Look under the Brantley Homecare tab at www.brantleycaregroup.example

Industry/Entity Type

Healthcare

Requirements
Must have
• • The Brantley Homecare company logo must be included.

```html
<!DOCTYPE html>
<html lang="en">
<head>
<meta charset="utf-8">
<title>Brantley Homecare – Tri-fold Brochure</title>
<link href="https://fonts.googleapis.com/css2?family=Open+Sans:ital,wght@0,400;0,600;0,700;1,400&display=swap" rel="stylesheet">
<style>
:root{
  --bg:#d9d9d9;
  --paper:#ffffff;
  --rose:#e8807a;
  --rose-mid:#f0a49d;
  --rose-soft:#f6c9c4;
  --charcoal:#4b4b4d;
  --charcoal-deep:#2f2f31;
  --ink:#333333;
  --leaf:#8fc06c;
  --leaf-deep:#5d8f3e;
  --skin:#d9a88a;
  --footer:#1f1f21;
}
*{box-sizing:border-box;margin:0;padding:0}
html,body{width:1200px;height:1089px;overflow:hidden}
body{background:var(--bg);font-family:"Open Sans",Arial,sans-serif;color:var(--ink);position:relative}
.spread{position:absolute;width:720px;height:509px;display:grid;grid-template-columns:repeat(3,1fr);background:var(--paper);box-shadow:0 6px 18px rgba(0,0,0,.35)}
.spread--outside{left:150px;top:30px}
.spread--inside{left:330px;top:560px}
.panel{position:relative;overflow:hidden;font-size:7.2px;line-height:1.45}
.panel p{margin-bottom:6px}
.header-rules{position:absolute;left:0;right:0;top:8px;height:10px;display:block}
.header-rules span{display:block;height:1.5px;margin-bottom:2.5px;background:var(--rose)}
.header-rules span:nth-child(2){background:var(--rose-mid)}
.header-rules span:nth-child(3){background:var(--rose-soft)}
.brand{position:absolute;right:10px;top:22px;display:flex;align-items:center;gap:3px;font-size:7px;font-weight:700;color:var(--rose)}
.brand__mark{width:7px;height:7px;background:var(--rose)}
.block{position:absolute;left:12px;right:12px}
.block--top{top:42px}
.block--bottom{top:236px}
.footer{position:absolute;left:0;right:0;bottom:0;height:22px;background:linear-gradient(var(--charcoal),var(--footer));color:#bbb;font-size:5.5px;padding:8px 10px}
.label{color:var(--rose);font-weight:600}
.section-title{color:var(--rose);font-size:12px;font-weight:600;margin:0 0 4px}
.photo{display:block;background:linear-gradient(135deg,var(--skin),#b98066 60%,#7d5a4a)}
.photo-strip{position:absolute;left:0;top:150px;width:480px;height:76px;display:flex;gap:2px;z-index:2}
.photo-strip .photo{flex:1}
.qa{background:var(--charcoal-deep);color:#eee;padding:8px}
.qa h3{font-size:7.5px;font-weight:700;margin-bottom:4px}
.qa p{margin-bottom:0}
.panel--qa{background:var(--charcoal);color:#eee}
.contact{position:absolute;left:22px;right:12px;bottom:40px;background:linear-gradient(#5a5a5c,#3a3a3c);border-radius:4px;padding:6px 10px;font-size:5.5px;color:#ddd;text-align:center}
.contact h4{font-size:7px;margin-bottom:2px;color:#fff}
.panel--cover{display:flex;flex-direction:column;background:#fff}
.cover-top{height:128px;background:linear-gradient(#e4f0d2,var(--leaf));display:flex;align-items:center;justify-content:center}
.cover-brand{display:flex;align-items:center;gap:6px;font-size:19px;font-weight:600;color:var(--rose)}
.cover-brand .brand__mark{width:14px;height:14px}
.cover-photo{height:150px;background:linear-gradient(160deg,var(--leaf-deep),var(--skin) 50%,var(--leaf-deep))}
.cover-band{height:34px;background:linear-gradient(var(--leaf),#6fa34d)}
.tagline{flex:1;background:linear-gradient(#555,#2a2a2a);color:#eee;font-style:italic;font-size:9.5px;padding:12px 14px;line-height:1.6}
.tagline span{display:block;padding-left:40px}
.panel--inside{padding:42px 12px 30px}
.panel--about h2{font-size:12px;font-weight:700;margin-bottom:6px}
.help-photo{height:72px;margin:6px -12px 8px}
.panel--hc{padding:42px 0 30px}
.hc-box{background:var(--charcoal);color:#eee;margin:0 10px;padding:8px 10px 10px}
.hc-box h2{color:var(--rose);font-size:12px;font-weight:700;text-align:center;margin-bottom:6px}
.hc-box ul{list-style:none}
.hc-photo{height:84px;margin-top:10px;background:linear-gradient(135deg,var(--rose),var(--skin) 60%,var(--rose-soft))}
.care-list{list-style:none;margin:4px 0 6px 8px}
.duo-photo{display:flex;gap:2px;height:58px;margin:8px -12px 0}
.duo-photo .photo{flex:1}
</style>
</head>
<body>

<section class="spread spread--outside">
  <article class="panel">
    <div class="header-rules"><span></span><span></span><span></span></div>
    <div class="brand"><span class="brand__mark"></span>Brantley Homecare</div>
    <div class="block block--top">
      <p><span class="label">Medication Services</span> – Our licensed nurse will pre-pour your medication in weekly pill containers for a 28-day period.</p>
      <p><span class="label">Transportation Services</span> – Our Care Professionals run errands or escort you to the grocery store, your personal appointments (physician, beautician, therapy), or other outings.</p>
    </div>
    <div class="block block--bottom">
      <h2 class="section-title">Your Schedule</h2>
      <p>Brantley Homecare is flexible with your care needs. As you need more or less care, your schedule can be adjusted to accommodate your needs. We have found that a set schedule works best (same days and times each week). This allows you to be able to depend on the same care professional(s) each week. You determine the schedule, from a minimum of four hours per shift to 24 hours of care per day, 7 days per week, 365 days per year. Our Scheduling department is available 24 hours per day.</p>
    </div>
    <div class="footer">www.brantleycaregroup.example</div>
  </article>

  <article class="panel panel--qa">
    <div class="header-rules"><span></span><span></span><span></span></div>
    <div class="brand"><span class="brand__mark"></span>Brantley Homecare</div>
    <div class="block block--top">
      <div class="qa">
        <h3>What makes Brantley Homecare different from other homecare agencies?</h3>
        <p>Answer: Brantley Homecare has earned a reputation in the community for providing compassionate, dependable, high quality home care services. We employ Care Professionals who embody the Brantley vision of consistent, outstanding service for every client.</p>
      </div>
    </div>
    <div class="block block--bottom">
      <div class="qa">
        <h3>Are your employees screened?</h3>
        <p>Answer: All of our Care Professionals are pre-screened and submit to a comprehensive testing and assessment process which includes their criminal and driving abstracts, as well as screenings through Child/Adult Protective Services.</p>
      </div>
    </div>
    <div class="contact">
      <h4>CONTACT US</h4>
      480 Harbor View Road, Suite 210, Lakeport, ST 00000<br>
      Phone (555) 014-2200<br>Fax (555) 014-2201<br>nora@brantleycare.example
    </div>
    <div class="footer"></div>
  </article>

  <article class="panel panel--cover">
    <div class="cover-top">
      <div class="cover-brand"><span class="brand__mark"></span>Brantley Homecare</div>
    </div>
    <div class="cover-photo" role="img" aria-label="Photo: a caregiver's hand gently holding an elderly client's hand"></div>
    <div class="cover-band"></div>
    <div class="tagline">Some one you can depend on <span>without question......</span></div>
    <div class="footer" style="background:var(--footer)">www.brantleycaregroup.example</div>
  </article>

  <div class="photo-strip">
    <span class="photo" role="img" aria-label="Photo: caregiver chatting with an elderly woman"></span>
    <span class="photo" role="img" aria-label="Photo: smiling nurse portrait"></span>
    <span class="photo" role="img" aria-label="Photo: caregiver assisting a senior at home"></span>
  </div>
</section>

<section class="spread spread--inside">
  <article class="panel panel--inside panel--about">
    <div class="header-rules"><span></span><span></span><span></span></div>
    <div class="brand"><span class="brand__mark"></span>Brantley Care Group</div>
    <h2>About Brantley Care Group</h2>
    <p>In 1996, Nora Brantley founded Brantley Homecare because of her own personal experience. Sixteen years later, in response to an overwhelming community need and countless client requests for a dedicated residential senior care home, she developed Brantley Senior Living. This is the second care resource offered under the expanded Brantley Care Group umbrella. With thousands of satisfied clients, and now an exciting new healthcare alternative, Brantley Care Group continues to stay focused on what we do best: take care of those who need us.</p>
    <p>Headquartered in Lakeport, the Brantley Care Group's Administrative Offices are located at 480 Harbor View Road, Suite 210. The Group serves the Lakeport community.</p>
    <div class="help-photo photo" role="img" aria-label="Photo: friendly caregiver beside a 'here to help' message"></div>
    <p>Nora Brantley, founder, president, and CEO of Brantley Care Group, discovered the need for dependable, compassionate home care at the tender age of 18, when she was seriously injured in an accident. Tragedy became inspiration, and in 1996, at the age of 21, she started Brantley Homecare.</p>
    <div class="footer">www.brantleycaregroup.example</div>
  </article>

  <article class="panel panel--hc">
    <div class="header-rules"><span></span><span></span><span></span></div>
    <div class="brand"><span class="brand__mark"></span>Brantley Homecare</div>
    <div class="hc-box">
      <h2>Brantley Home Care</h2>
      <p>Brantley Homecare is a state licensed private duty home health care agency serving the Lakeport community since 1996.</p>
      <p>We provide in-home services ranging from light housekeeping to personal care and skilled nursing. We strive to give compassionate, dependable care of the highest quality while maintaining extremely competitive rates. Everything we do is geared toward meeting the individual needs of our clients.</p>
      <p>Whether you need a little help or a lot of help, you'll find that Brantley Homecare's services are a cut above the rest. The Brantley Way is special; it is compassionate, professional, dependable, and flexible.</p>
      <p><strong>All of our Care Professionals:</strong></p>
      <ul>
        <li>Are bonded, insured, and supervised;</li>
        <li>Have passed both criminal and abuse background checks;</li>
        <li>Have been screened for TB;</li>
        <li>Are certified in CPR and First Aid</li>
      </ul>
    </div>
    <div class="hc-photo" role="img" aria-label="Photo: caregiver sharing a warm moment with a client"></div>
    <div class="footer">www.brantleycaregroup.example</div>
  </article>

  <article class="panel panel--inside">
    <div class="header-rules"><span></span><span></span><span></span></div>
    <div class="brand"><span class="brand__mark"></span>Brantley Homecare</div>
    <p>All client care is supervised by a licensed Nurse Care Consultant whose duties include:</p>
    <ul class="care-list">
      <li>Regular home visits</li>
      <li>Client evaluation</li>
      <li>Care Professional supervision</li>
      <li>Revising/updating client care plans</li>
      <li>24/7 phone support</li>
    </ul>
    <h2 class="section-title">Services</h2>
    <p>Brantley Homecare provides two different levels of care. Our Nurse Care Consultant will assist the client and family in determining the appropriate level of care needed during the complimentary initial consultation.</p>
    <p><span class="label">Home Aide Care</span> – Our Care Professionals provide personal care needs, provide companionship, run errands, and do light housekeeping along with assisting you with the activities of daily living.</p>
    <p><span class="label">Skilled Nursing Care</span> – We offer a wide range of skilled nursing services using RN's and LPN's who provide treatment from wound care to life support, in addition to all of the services performed by our Nurse Aides.</p>
    <div class="duo-photo">
      <span class="photo" role="img" aria-label="Photo: nurse helping a senior man"></span>
      <span class="photo" role="img" aria-label="Photo: caregiver and elderly client smiling together"></span>
    </div>
    <div class="footer">www.brantleycaregroup.example</div>
  </article>
</section>

</body>
</html>
```